Coastal Learner Bureau business cards

Australian company about to start offering its services. We recruit international students to come to study English, vocational education and postgraduate courses in Australia. We help them find the institution and select the right city they want to come to Australia. We are a young, online oriented and supportive agency. Our clients are between 18 and 35 years old, mainly University students, young professionals or people with work experience. We provide much more information that any other agency offer. We administrate a Facebook group with more than 11.000 members that daily ask questions about general information when coming to Australia, while they are here and even after they leave the country

Target Market(s)

International students from South America, Central America and Europe

Industry/Entity Type

Student

Contact Information for Business Card

Tomas Bilbrea
Managing Director
tomas@kelvarin.com.au
www.kelvoria.com.au
+61 491058264
Melbourne, Australia

Font styles to use
Serif
Sans Serif

Colors

Designer to choose colors to be used in the design.

Requirements
Must have
• Horizontal design
• Standard business card size and shape. If font uses green or yellow colours, they will have to match the ones from the logo
Nice to have
• UPDATE: Use the contents of the green image to design one of the card sides. Use our logo in the background of that side as watermark.
• Passport image, or immigration stamps. A picture of the Yarra River (from Melbourne) would be cool as well.
Should not have
• Non-standard business card size and shape
• Not black as the background colour of any sides as we are not a VIP agency or a hight class service. We are orientes to young people and they like colours, pictures, something attractive.
• Vertical design
• NO YELLOW or BLACK AS THE BACKGROUND COLOUR OF ANY SIDE OF THE BIZ CARD

```html
<!DOCTYPE html>
<html lang="en">
<head>
<meta charset="utf-8">
<title>Coastal Learner Bureau business cards</title>
<link href="https://fonts.googleapis.com/css2?family=Open+Sans:wght@400;600;700&display=swap" rel="stylesheet">
<style>
  :root {
    --stage: #2e2e2e;
    --card: #1f6b3a;
    --card-edge: #2a7e48;
    --yellow: #f2c200;
    --text-light: #f1f5f0;
    --divider: #3a8a55;
  }
  * { margin: 0; padding: 0; box-sizing: border-box; }
  html, body {
    width: 1200px; height: 899px; overflow: hidden;
    background: var(--stage);
    font-family: "Open Sans", Arial, sans-serif;
  }
  .stage {
    position: relative; width: 1200px; height: 899px;
    display: flex; align-items: center; justify-content: center; gap: 60px;
  }
  .card {
    position: relative; width: 500px; height: 286px;
    background: var(--card);
    border: 1px solid var(--card-edge);
    border-radius: 22px;
    box-shadow: 0 14px 30px rgba(0,0,0,.45);
    overflow: hidden;
  }
  .card-front { display: flex; }
  .front-brand {
    width: 52%; display: flex; align-items: center; justify-content: center;
    border-right: 1px solid var(--divider);
  }
  .brand-name {
    color: var(--yellow); font-weight: 700; font-size: 38px; letter-spacing: .5px;
  }
  .front-details {
    width: 48%; padding: 48px 0 0 26px; color: var(--text-light); font-size: 13px;
  }
  .person-name { color: var(--yellow); font-weight: 700; font-size: 17px; line-height: 1.2; }
  .person-role { font-size: 13px; margin-bottom: 20px; }
  .location { margin-bottom: 14px; }
  .contact-list { list-style: none; }
  .contact-list li { display: flex; align-items: center; gap: 10px; line-height: 22px; white-space: nowrap; }
  .contact-list svg { width: 11px; height: 11px; flex: none; }
  .card-back {
    display: flex; flex-direction: column; align-items: center; justify-content: center;
  }
  .card-back .brand-name { font-size: 44px; margin-top: -20px; }
  .tagline {
    color: var(--yellow); font-weight: 600; font-size: 14px; margin-top: 40px;
  }
</style>
</head>
<body>
<main class="stage">
  <section class="card card-front" aria-label="Card front">
    <div class="front-brand">
      <span class="brand-name">Kelvoria</span>
    </div>
    <div class="front-details">
      <p class="person-name">Tomas Bilbrea</p>
      <p class="person-role">Managing Director</p>
      <p class="location">Melbourne, Australia</p>
      <ul class="contact-list">
        <li>
          <svg viewBox="0 0 12 12" aria-hidden="true"><path fill="var(--yellow)" d="M2.5 0.8 4.3 3.2 3.3 4.4c.7 1.6 2.1 3 3.7 3.7l1.2-1L10.6 8.9 9.4 11C5 10.6 1.3 6.9 1 2.5z"/></svg>
          +61 491058264
        </li>
        <li>
          <svg viewBox="0 0 12 12" aria-hidden="true"><rect x="0.5" y="2" width="11" height="8" fill="var(--yellow)"/><path d="M0.8 2.4 6 6.5l5.2-4.1" stroke="var(--card)" stroke-width="1.2" fill="none"/></svg>
          tomas@kelvarin.com.au
        </li>
        <li>
          <svg viewBox="0 0 12 12" aria-hidden="true"><circle cx="6" cy="6" r="5.5" fill="var(--yellow)"/><path d="M0.8 6h10.4M6 0.5c-2.6 3-2.6 8 0 11M6 0.5c2.6 3 2.6 8 0 11" stroke="var(--card)" stroke-width=".9" fill="none"/></svg>
          www.kelvoria.com.au
        </li>
      </ul>
    </div>
  </section>

  <section class="card card-back" aria-label="Card back">
    <span class="brand-name">Kelvoria</span>
    <p class="tagline">Hacemos más por ti!</p>
  </section>
</main>
</body>
</html>
```